Emerging automotive detailing business

I am starting a small automotive detailing business in hopes of becoming a well-known detailer to work on high end cars. I would like a card to reflect the high quality and time I put into my work. The name of the company is Bright Crest Detailing. I feel like it represents racecars getting off the line at the drag strip as well as an innuendo of "Up the Ladder". I do minor paint correction such as clay barring, multi-step buffing and polishing, waxing, hand washes, etc. I am always striving to learn more and improve my work. My goal is to have total customer satisfaction. This is a female run business but I do not want it to be very girly. Elegant is okay! I have pictures of my personal wrenfield attached, they do not need to be incorporated but if you can think of a cool way to use 1 or all of them, go for it!

Target Market(s)

Anyone that owns a vehicle. Preferably high end vehicles such as Valtori, Castellverde and Morvani but I will also happily work on any car, truck or suv no matter what brand.

Industry/Entity Type

Automotive

Contact Information for Business Card

Bright Crest Detailing
Mira Tolland
4175 Quenhollow Rd
Ashmere PA 17492
Cell phone- call/text- 717-555-0148
email- brightcrestdetails@maildrop-example.com
Instagram: @brightcrestdetailing
Facebook: facebook.com/brightcrestdetailing

Requirements
Must have
• Business name, my name, address, phone number. Listing that I do minor paint correction such as clay barring, multi-step buffing and polishing, waxing, hand washes, interior cleaning, and more. (This last part was in nice to haves but I have realized that I do really want it, so I moved it to must haves.) I want something that is different and eye-catching to my customers. Some people have done this very well with cards already submitted to me, but a lot have not. I didn't mess with the "look and feel bars" much because because I am pretty open to the overall design as long as it is not your basic run of the mill design.
Nice to have
• Something car related. Maybe an appointment time/date line. I do not have a logo, but if you would like to design one and incorporate it, that would be amazing!
Should not have
• Purple and Pink colors. Boring, basic, normal card.

```html
<!DOCTYPE html>
<html lang="en">
<head>
<meta charset="utf-8">
<title>Bright Crest Detailing – Business Card</title>
<link rel="stylesheet" href="https://fonts.googleapis.com/css2?family=Tinos:wght@700&family=Exo+2:wght@600&family=Arimo:wght@400;700&display=swap">
<style>
  :root {
    --steel: #1d3557;
    --ink: #000000;
    --paper: #ffffff;
    --silver: #c9ced6;
    --backdrop: #e4e4e4;
  }
  html, body {
    margin: 0;
    width: 1189px;
    height: 1200px;
    overflow: hidden;
    background: var(--backdrop);
  }
  .card {
    position: absolute;
    left: 140px;
    width: 918px;
    height: 524px;
    box-shadow: 0 4px 14px rgba(0,0,0,0.25);
  }
  .card svg { display: block; width: 100%; height: 100%; }
  .card--front { top: 45px; }
  .card--back { top: 623px; }
  .brand-title {
    font-family: "Tinos", "Times New Roman", serif;
    font-weight: 700;
  }
  .holder-name {
    font-family: "Exo 2", "Arial", sans-serif;
    font-weight: 600;
    font-size: 52px;
    fill: var(--paper);
  }
  .contact-line {
    font-family: "Arimo", "Arial", sans-serif;
    font-size: 29px;
    fill: var(--paper);
  }
  .services-heading {
    font-family: "Arimo", "Arial", sans-serif;
    font-weight: 700;
    font-size: 34px;
    letter-spacing: 4px;
    fill: var(--paper);
  }
  .service-line {
    font-family: "Arimo", "Arial", sans-serif;
    font-size: 30px;
    fill: var(--silver);
  }
</style>
</head>
<body>

<div class="card card--front">
  <svg viewBox="0 0 1125 642" xmlns="http://www.w3.org/2000/svg">
    <rect class="card-base" width="1125" height="642" fill="var(--paper)"/>
    <text class="brand-title" x="562" y="213" font-size="78" text-anchor="middle" fill="var(--ink)">Bright Crest Detailing</text>

    <polygon class="accent-band" points="60,332 134,357 994,357 1065,332 994,373 134,373" fill="var(--ink)"/>
    <polygon class="contact-panel" points="0,313 134,387 994,387 1125,314 1125,642 0,642" fill="var(--steel)"/>

    <text class="holder-name" x="40" y="530">Mira Tolland</text>
    <rect class="divider" x="428" y="423" width="3" height="183" fill="var(--paper)"/>

    <g class="contact-icons" fill="var(--paper)">
      <rect x="447" y="430" width="24" height="22" rx="2"/>
      <path d="M452 446 h14 v-4 l-3 -4 h-8 l-3 4z M451 437 q8 -6 16 0 v2 h-4 v-2 h-8 v2 h-4z" fill="var(--steel)"/>
      <rect x="447" y="476" width="24" height="22" rx="2"/>
      <rect x="447" y="524" width="24" height="22" rx="2"/>
      <path d="M450 529 h18 v12 h-18z" fill="var(--steel)"/>
      <path d="M450 529 l9 7 l9 -7" stroke="var(--paper)" stroke-width="1.6" fill="none"/>
      <rect x="447" y="572" width="24" height="22" rx="2"/>
      <path d="M459 590 l-5 -8 a5 5 0 1 1 10 0z" fill="var(--steel)"/>
      <circle cx="459" cy="580" r="1.8" fill="var(--paper)"/>
    </g>

    <g class="contact-list">
      <text class="contact-line" x="491" y="452">717-555-0148</text>
      <text class="contact-line" x="491" y="498">@brightcrestdetailing</text>
      <text class="contact-line" x="491" y="546" textLength="600" lengthAdjust="spacingAndGlyphs">brightcrestdetails@maildrop-example.com</text>
      <text class="contact-line" x="491" y="594">4175 Quenhollow Rd, Ashmere PA 17492</text>
    </g>
  </svg>
</div>

<div class="card card--back">
  <svg viewBox="0 0 1125 642" xmlns="http://www.w3.org/2000/svg">
    <rect class="card-base" width="1125" height="642" fill="var(--ink)"/>

    <text class="services-heading" x="562" y="125" text-anchor="middle">MINOR PAINT CORRECTION</text>

    <rect class="pinstripe" y="221" width="1125" height="3" fill="var(--paper)"/>
    <rect class="name-band" y="238" width="1125" height="166" fill="var(--paper)"/>
    <rect class="pinstripe" y="415" width="1125" height="3" fill="var(--paper)"/>
    <text class="brand-title" x="562" y="346" font-size="92" text-anchor="middle" fill="var(--steel)">Bright Crest Detailing</text>

    <g class="services-list">
      <text class="service-line" x="562" y="505" text-anchor="middle">Clay Barring · Multi-Step Buffing &amp; Polishing · Waxing</text>
      <text class="service-line" x="562" y="553" text-anchor="middle">Hand Washes · Interior Cleaning · And More</text>
    </g>
  </svg>
</div>

</body>
</html>
```